Verodex business card

Business card for sustainable investment company called "Verodex". Verodex is an exchange platform selling carbon credits between buyers and sellers. Carbon Credits are an environmental commodity for reducing global carbon emissions.

the card should obviously have our logo and the theme should be sustainability/environment mixed with a trading platform.

Contact Information for Business Card

Logo, Name, Title, Phone, Email

Colors
0054AA
0677BA
7BADD7
CADEEF
E8F1F8
0094D4
00A9DD
6FCCEA
C7EBF8
E9F6FB
00AB8E
00BBA5
67D7C9
C6EFE9
E9F9F6
59FF00
82FF00
B8FF75
E3FFCB
F4FFEA

```html
<!DOCTYPE html>
<html lang="en">
<head>
<meta charset="utf-8">
<title>Verodex Business Card</title>
<link href="https://fonts.googleapis.com/css2?family=Montserrat:wght@500;600;700&display=swap" rel="stylesheet">
<style>
  :root {
    --navy: #13284f;
    --white: #ffffff;
    --stage: #e6e8ec;
    --accent-light: #6fccea;
    --accent-mid: #00a9dd;
    --accent-deep: #0054aa;
  }
  * { margin: 0; padding: 0; box-sizing: border-box; }
  html, body { width: 1200px; height: 900px; overflow: hidden; }
  body {
    background: var(--stage);
    font-family: "Montserrat", sans-serif;
    display: flex;
    flex-direction: column;
    align-items: center;
    justify-content: center;
    gap: 56px;
  }
  .card {
    position: relative;
    width: 600px;
    height: 343px;
    overflow: hidden;
    box-shadow: 0 8px 24px rgba(0,0,0,0.18);
  }
  .card-front { background: var(--navy); display: flex; align-items: center; justify-content: center; }
  .card-back { background: var(--white); }
  .brand { display: flex; align-items: center; gap: 18px; }
  .brand-dot { width: 44px; height: 44px; border-radius: 50%; background: var(--accent-mid); }
  .brand-name { font-weight: 600; letter-spacing: 0.04em; }
  .card-front .brand-name { color: var(--white); font-size: 58px; }
  .card-back .brand { position: absolute; left: 44px; top: 132px; gap: 12px; }
  .card-back .brand-dot { width: 30px; height: 30px; }
  .card-back .brand-name { color: var(--navy); font-size: 34px; }
  .wave { position: absolute; inset: 0; width: 100%; height: 100%; }
  .holder {
    position: absolute;
    right: 30px;
    top: 130px;
    text-align: right;
    color: var(--white);
  }
  .holder-name { font-weight: 700; font-size: 18px; letter-spacing: 0.01em; text-transform: uppercase; white-space: nowrap; }
  .holder-title { font-weight: 500; font-size: 13px; margin-top: 2px; }
  .contact-list { list-style: none; margin-top: 26px; }
  .contact-item {
    display: flex;
    justify-content: flex-end;
    align-items: center;
    gap: 10px;
    font-size: 13px;
    font-weight: 500;
    line-height: 22px;
  }
  .contact-icon { width: 14px; height: 14px; fill: var(--white); }
</style>
</head>
<body>
  <section class="card card-front">
    <div class="brand">
      <span class="brand-dot"></span>
      <span class="brand-name">VERODEX</span>
    </div>
  </section>

  <section class="card card-back">
    <svg class="wave" viewBox="0 0 600 343" preserveAspectRatio="none" aria-hidden="true">
      <defs>
        <linearGradient id="accentSweep" x1="0" y1="1" x2="1" y2="0">
          <stop offset="0" stop-color="var(--accent-light)"/>
          <stop offset="0.45" stop-color="var(--accent-mid)"/>
          <stop offset="1" stop-color="var(--accent-deep)"/>
        </linearGradient>
      </defs>
      <path fill="url(#accentSweep)" d="M600 -4 C436 22 366 86 326 156 C286 226 196 306 40 343 L66 343 C206 314 294 236 334 166 C374 96 444 34 600 4 Z"/>
      <path fill="var(--navy)" d="M600 14 C450 40 380 100 340 170 C300 240 210 318 90 343 L600 343 Z"/>
    </svg>

    <div class="brand">
      <span class="brand-dot"></span>
      <span class="brand-name">VERODEX</span>
    </div>

    <div class="holder">
      <p class="holder-name">Daniel Hartwell</p>
      <p class="holder-title">Co-Founder</p>
      <ul class="contact-list">
        <li class="contact-item">308-555-0142
          <svg class="contact-icon" viewBox="0 0 16 16"><path d="M3 1h3l1.5 4-2 1.3a9 9 0 0 0 4.2 4.2L11 8.5l4 1.5v3a2 2 0 0 1-2 2A12 12 0 0 1 1 3a2 2 0 0 1 2-2z"/></svg>
        </li>
        <li class="contact-item">info@verodex.com
          <svg class="contact-icon" viewBox="0 0 16 16"><path d="M1 3h14v10H1z M1.8 3.8 8 9l6.2-5.2" fill="none" stroke="#fff" stroke-width="1.4"/></svg>
        </li>
        <li class="contact-item">www.verodex.com
          <svg class="contact-icon" viewBox="0 0 16 16"><circle cx="8" cy="8" r="6.5" fill="none" stroke="#fff" stroke-width="1.3"/><ellipse cx="8" cy="8" rx="2.8" ry="6.5" fill="none" stroke="#fff" stroke-width="1.1"/><path d="M1.5 8h13" stroke="#fff" stroke-width="1.1"/></svg>
        </li>
      </ul>
    </div>
  </section>
</body>
</html>
```